Brightfield Ventures Inc. Letterhead

Creation of attractive and eye catching letterhead for a business start-up for the construction industry. Letterhead must relate to construction, but avoid standard hammer and tools in the design.

I forgot to add some details, sorry about that. Some pertinent info: Ph: 916-555-0187 brightfieldventures.example 448 Willowmere Ave, Ste 210 Folsom, CA 95999 info@brightfieldventures.example not sure if slogan should be in there" “Connecting construction professionals to create a purpose driven industry.” must be able to be used in word. Thanks!

```html
<!DOCTYPE html>
<html lang="en">
<head>
<meta charset="utf-8">
<title>Brightfield Ventures Inc. Letterhead</title>
<link rel="stylesheet" href="https://fonts.googleapis.com/css2?family=Open+Sans:wght@400;600;700&family=Arimo:wght@700&display=swap">
<style>
  :root {
    --backdrop: #e4e5e6;
    --paper: #fafafa;
    --ink: #3a3a3a;
    --navy: #1f2a6b;
    --red: #d7262e;
    --muted: #555;
    --faint: rgba(31, 42, 107, 0.07);
  }
  html, body {
    margin: 0;
    width: 1200px;
    height: 945px;
    overflow: hidden;
    background: var(--backdrop);
  }
  .letterhead {
    position: absolute;
    left: 282px;
    top: 22px;
    width: 636px;
    height: 900px;
    background: var(--paper);
    box-shadow: 0 6px 24px rgba(0,0,0,0.12);
    font-family: "Open Sans", sans-serif;
    color: var(--ink);
    box-sizing: border-box;
    padding: 56px 72px 0 72px;
    overflow: hidden;
  }
  .brand {
    display: flex;
    align-items: center;
    gap: 8px;
    border-bottom: 1.5px solid var(--red);
    padding-bottom: 6px;
    width: max-content;
  }
  .brand-mark {
    width: 12px;
    height: 12px;
    background: var(--red);
  }
  .brand-name {
    font-weight: 700;
    font-size: 15px;
    letter-spacing: 1.5px;
    color: var(--navy);
    text-transform: uppercase;
  }
  .salutation {
    margin: 92px 0 14px 18px;
    font-family: "Arimo", sans-serif;
    font-weight: 700;
    font-size: 14px;
    color: #222;
  }
  .body-copy {
    margin-left: 30px;
    font-size: 11.5px;
    line-height: 1.32;
    text-align: justify;
  }
  .body-copy p { margin: 0 0 14px 0; }
  .signature {
    margin: 58px 0 0 34px;
    width: 130px;
    height: 42px;
    background: linear-gradient(90deg, #d8d8d8, #ececec);
    border-radius: 4px;
  }
  .watermark {
    position: absolute;
    right: 40px;
    bottom: 170px;
    font-weight: 700;
    font-size: 26px;
    letter-spacing: 2px;
    color: var(--faint);
    text-transform: uppercase;
  }
  .footer {
    position: absolute;
    left: 0;
    right: 0;
    bottom: 34px;
    text-align: center;
    font-size: 10px;
    color: var(--muted);
    line-height: 1.6;
  }
  .footer .contact { display: inline-flex; gap: 12px; align-items: center; }
  .footer .item { display: inline-flex; align-items: center; gap: 3px; }
  .footer svg { width: 9px; height: 9px; fill: var(--red); }
</style>
</head>
<body>
  <main class="letterhead">
    <header class="brand">
      <span class="brand-mark"></span>
      <span class="brand-name">Brightfield Ventures</span>
    </header>

    <p class="salutation">Dear Mr. John,</p>

    <section class="body-copy">
      <p>Lorem Ipsum is simply dummy text of the printing and typesetting industry. Lorem Ipsum has been the industry's standard dummy text ever since the 1500s, when an unknown printer took a galley of type and scrambled it to make a type specimen book. It has survived not only five centuries, but also the leap into electronic typesetting, remaining essentially unchanged.</p>
      <p>The standard chunk of Lorem Ipsum used since the 1500s is reproduced below for those interested. Sections 1.10.32 and 1.10.33 from "de Finibus Bonorum et Malorum" by Cicero are also reproduced in their exact original form, accompanied by English versions from the 1914 translation by H. Rackham</p>
      <p>Lorem Ipsum is simply dummy text of the printing and typesetting industry. Lorem Ipsum has been the industry's standard dummy text ever since the 1500s, when an unknown printer took a galley of type and scrambled it to make a type specimen book. It has survived not only five centuries, but also the leap into electronic typesetting, remaining essentially unchanged. It was popularised in the</p>
      <p>The standard chunk of Lorem Ipsum used since the 1500s is reproduced below for those interested. Sections 1.10.32 and 1.10.33 from "de Finibus Bonorum et Malorum" by Cicero are also reproduced in their exact original form, accompanied by English versions from the 1914 translation by H. Rackham</p>
      <p>The standard chunk of Lorem Ipsum used since the 1500s is reproduced below for those interested. Sections 1.10.32 and 1.10.33 from "de Finibus Bonorum et Malorum" by Cicero are also reproduced in their exact original form.</p>
    </section>

    <div class="signature" role="img" aria-label="Handwritten signature"></div>

    <div class="watermark" aria-hidden="true">Brightfield</div>

    <footer class="footer">
      <div>Po. box 201, Street Name, City Name, Zip Code - 00000</div>
      <div class="contact">
        <span class="item"><svg viewBox="0 0 10 10"><path d="M2 1h2l1 2-1 1c.5 1 1 1.5 2 2l1-1 2 1v2c0 .5-.5 1-1 1C4 9 1 6 1 2c0-.5.5-1 1-1z"/></svg>1-254-555-0142</span>
        <span class="item"><svg viewBox="0 0 10 10"><path d="M1 2h8v6H1z M1 2l4 3 4-3" stroke="#fafafa" stroke-width=".6"/></svg>info@companyname.example</span>
        <span class="item"><svg viewBox="0 0 10 10"><circle cx="5" cy="5" r="4"/></svg>www.companyname.example</span>
      </div>
    </footer>
  </main>
</body>
</html>
```